Climbing Gear Company Stationary Design

We need some new stationary to standardise our business.
We require:

Business Card
A4 Letterhead
With complements slip

Our business is a Distributor and retailer of rock climbing equipment throughout Australia.
We need to the stationary (business card in particular) to reflect this.

Target Market(s)

customers, other retail outlets, overseas manufacturers.

Industry/Entity Type

Business

Requirements
Must have
• company logo
website url- www.ridgetopgearworks.com.au
email - mark@ridgetopgearworks.com
Business Address: Unit 3, 14-16 Marlowe Street, Coffs Harbour, NSW, 2371
Phone: 0438 627 194
my Name (on Business card) - Gordon Pellimore
use of Blue colour in our logo

```html
<!DOCTYPE html>
<html lang="en">
<head>
<meta charset="utf-8">
<title>Ridgetop Gearworks – Business Card</title>
<link rel="stylesheet" href="https://fonts.googleapis.com/css2?family=Open+Sans:wght@400;600;700&display=swap">
<style>
  :root {
    --brand-blue: #233f8b;
    --text-grey: #4a4a4a;
    --rule-grey: #c9c9c9;
    --card-white: #ffffff;
    --backdrop: #efece6;
    --card-shadow: rgba(0, 0, 0, 0.18);
  }
  * { box-sizing: border-box; margin: 0; padding: 0; }
  html, body {
    width: 1200px;
    height: 483px;
    overflow: hidden;
  }
  body {
    position: relative;
    background: var(--backdrop);
    font-family: "Open Sans", Arial, sans-serif;
  }
  .card {
    position: absolute;
    background: var(--card-white);
    box-shadow: 2px 4px 10px var(--card-shadow);
  }
  .card--contact { left: 56px; top: 92px; width: 525px; height: 299px; }
  .card--brand { left: 612px; top: 90px; width: 524px; height: 298px; }

  .wordmark {
    position: absolute;
    display: flex;
    align-items: center;
    justify-content: center;
    font-weight: 700;
    text-transform: uppercase;
    letter-spacing: 0.01em;
    white-space: nowrap;
    color: var(--brand-blue);
  }
  .wordmark__dot {
    display: inline-block;
    background: var(--brand-blue);
    border-radius: 50%;
  }

  .card--contact .wordmark {
    left: 28px; top: 130px; width: 240px;
    font-size: 19px; line-height: 24px; gap: 6px;
  }
  .card--contact .wordmark__dot { width: 10px; height: 10px; }

  .divider {
    position: absolute;
    left: 288px;
    top: 86px;
    width: 1px;
    height: 124px;
    background: var(--rule-grey);
  }
  .contact {
    position: absolute;
    left: 308px;
    top: 86px;
    font-size: 11.5px;
    line-height: 17px;
    color: var(--text-grey);
  }
  .contact__name {
    font-size: 14px;
    color: var(--brand-blue);
    text-transform: uppercase;
    letter-spacing: 0.02em;
    margin-bottom: 12px;
  }
  .contact__address { margin-bottom: 10px; }

  .card--brand .wordmark {
    left: 62px; top: 134px; width: 400px;
    font-size: 27px; line-height: 34px; gap: 9px;
  }
  .card--brand .wordmark__dot { width: 14px; height: 14px; }

  .web-address {
    position: absolute;
    left: 0;
    top: 246px;
    width: 100%;
    text-align: center;
    font-size: 14px;
    letter-spacing: 0.16em;
    color: var(--brand-blue);
  }
</style>
</head>
<body>
  <section class="card card--contact">
    <div class="wordmark"><span class="wordmark__dot"></span>Ridgetop Gearworks</div>
    <div class="divider"></div>
    <div class="contact">
      <p class="contact__name">Gordon Pellimore</p>
      <p class="contact__address">Unit 3, 14-16 Marlowe Street<br>Coffs Harbour, NSW, 2371</p>
      <p class="contact__lines">P : 0438 627 194<br>E : mark@ridgetopgearworks.com<br>W: www.ridgetopgearworks.com.au</p>
    </div>
  </section>

  <section class="card card--brand">
    <div class="wordmark"><span class="wordmark__dot"></span>Ridgetop Gearworks</div>
    <p class="web-address">www.ridgetopgearworks.com.au</p>
  </section>
</body>
</html>
```